Onsite Energy for Retail Tenants

Need a short one page-3 part build showing how the program for discounted clean energy works - moving into a call to action with multiple links.

1) Solar Garden Produces Energy
2) Credits Available for Tenants’ Utility Bills
3) Sign Up to Receive Utility Bill Credits.
Save 5%

This document will be used:
1) Embedded in Mailchimp emails
2) as an html landing page
3) as an image

Use the latest powerpoint Tenant slide E as guidance
Updates

Infographic is simplistic. 3 part build using graphics and information. Flow is really important so Gifs welcome.

Target Market(s)

Owners of small stores throughout the US.

Industry/Entity Type

Real Estate

Colors

Designer to choose colors to be used in the design.

Requirements
Must have
• It must explain the program clearly and succinctly using the language from the first slide of Mockup 1. This slide must become an elegant build for the 3 step process. See Mockup 2 for its cleanliness ideas for a similar but different program.
• The second slide of mockup 1 is the call to action and must have clickable links and promote trust.
• Please use the attached font styles.
• The text is sparse and so needs to be bold and in order and with the graphics needs to explain how it works perfectly.
• The graphics should be clean and sophisticated but the message and flow needs to be simple.
Nice to have
• Moving arrows to show flow of energy and credits.
• Ability to switch out language of text.

```html
<!DOCTYPE html>
<html lang="en">
<head>
<meta charset="utf-8">
<title>How Clean Discount Electricity Works</title>
<link href="https://fonts.googleapis.com/css2?family=Montserrat:wght@400;500;600;700;800&display=swap" rel="stylesheet">
<style>
  :root{
    --navy:#1d3557;
    --ink:#333d47;
    --muted:#5b6670;
    --orange:#f39a1e;
    --orange-dark:#e07d10;
    --green:#3a9d46;
    --sky:#e8f2fb;
    --band:#2f6fae;
    --band-light:#4a86c4;
    --paper:#ffffff;
    --line:#d6dde4;
  }
  *{box-sizing:border-box;margin:0;padding:0}
  html,body{width:720px;height:1200px;overflow:hidden;background:var(--paper)}
  body{font-family:"Montserrat",Arial,sans-serif;color:var(--ink);position:relative}

  .page-title{position:absolute;top:14px;left:0;width:720px;text-align:center;
    font-size:33px;font-weight:800;color:var(--navy);letter-spacing:-.3px}

  .hero{position:absolute;top:66px;left:0;width:720px;height:336px}
  .hero-art{position:absolute;left:30px;top:70px;width:520px;height:240px;border-radius:6px;
    background:linear-gradient(160deg,#cfe3f5 0%,#f2d7b3 45%,#b98a5a 100%)}
  .hero-sun{position:absolute;left:10px;top:0;width:110px;height:110px;border-radius:50%;
    background:radial-gradient(circle,#ffd54a 0%,#f6b21e 70%,rgba(246,178,30,0) 72%)}
  .hero-people{position:absolute;right:28px;top:196px;width:118px;height:110px;border-radius:6px;
    background:linear-gradient(180deg,#f5e2c6,#d7a36b)}
  .hero-arrows{position:absolute;left:0;top:0}
  .callout{position:absolute;font-weight:700;line-height:1.2}
  .callout.solar{left:130px;top:10px;width:230px;font-size:19px;color:var(--orange)}
  .callout.credits{left:380px;top:4px;width:200px;font-size:18px;color:var(--green);text-align:center}
  .callout.signup{left:546px;top:74px;width:170px;font-size:17px;color:var(--orange)}

  .how-steps{position:absolute;top:410px;left:24px;width:672px;display:flex;justify-content:space-between}
  .how-step{width:210px;text-align:center}
  .how-step h3{font-size:15px;font-weight:700;color:var(--navy);margin-bottom:5px}
  .how-step p{font-size:9.5px;line-height:1.35;color:var(--muted)}

  .offer-band{position:absolute;top:494px;left:0;width:720px;height:64px;text-align:center;
    background:linear-gradient(90deg,#fbd48a,var(--orange) 50%,#fbd48a)}
  .offer-band h2{font-size:29px;font-weight:800;color:var(--navy);padding-top:6px;line-height:1.1}
  .offer-band p{font-size:15px;font-weight:600;color:var(--navy)}

  .signup-steps{position:absolute;top:570px;left:0;width:720px;height:320px}
  .step-label{position:absolute;font-size:34px;font-weight:800;color:var(--navy)}
  .step-one{left:28px;top:0}
  .step-two{right:34px;top:14px}
  .step-text{position:absolute;font-size:13px;line-height:1.45;color:var(--ink)}
  .step-text.one{left:28px;top:62px;width:230px}
  .step-text.two{left:470px;top:164px;width:226px}
  .guarantee{position:absolute;left:28px;top:150px;background:var(--orange);color:#fff;
    font-size:11px;font-weight:700;padding:6px 12px;border-radius:3px}
  .hex-center{position:absolute;left:300px;top:40px}
  .panel-art{position:absolute;left:470px;top:66px;width:140px;height:90px;border-radius:4px;
    background:linear-gradient(160deg,#ffe39a 0%,#2e5e93 55%,#1d3557 100%)}

  .benefits{position:absolute;top:902px;left:0;width:720px;height:122px;
    background:linear-gradient(90deg,var(--band),var(--band-light));
    display:grid;grid-template-columns:1fr 1fr;padding:16px 40px;row-gap:14px;column-gap:30px}
  .benefit{display:flex;align-items:center;gap:12px;color:#fff;font-size:14px;font-weight:600;line-height:1.25}
  .benefit svg{flex:none}

  .cta{position:absolute;top:1036px;left:0;width:720px;display:flex;justify-content:center;gap:30px}
  .cta a{display:flex;align-items:center;justify-content:center;gap:10px;text-decoration:none;
    height:64px;font-weight:700;font-size:20px;border-radius:4px}
  .cta .learn{width:250px;background:var(--navy);color:#fff;line-height:1.1;text-align:center}
  .cta .contact{width:250px;background:var(--orange);color:#fff}

  .footer{position:absolute;top:1124px;left:0;width:720px;height:76px;border-top:1px solid var(--line);
    display:flex;align-items:center;justify-content:space-between;padding:0 28px}
  .brand{display:flex;align-items:center;gap:8px;font-size:20px;font-weight:700;color:var(--navy)}
  .brand-dot{width:18px;height:18px;border-radius:50%;background:var(--orange)}
  .copyright{font-size:12px;color:var(--muted)}
</style>
</head>
<body>
  <h1 class="page-title">How Clean Discount Electricity Works?</h1>

  <section class="hero">
    <div class="hero-sun" role="img" aria-label="Glowing sun above the shopping centre"></div>
    <div class="hero-art" role="img" aria-label="Illustration of a strip mall with solar panels on its roof"></div>
    <div class="hero-people" role="img" aria-label="Illustration of a tenant reviewing a utility bill"></div>
    <svg class="hero-arrows" width="720" height="336" viewBox="0 0 720 336" aria-hidden="true">
      <path d="M250 62 C300 100 330 120 380 110" fill="none" stroke="var(--orange)" stroke-width="3" stroke-dasharray="7 6"/>
      <path d="M470 58 C510 80 520 100 546 110" fill="none" stroke="var(--green)" stroke-width="3" stroke-dasharray="7 6"/>
      <path d="M610 140 C640 160 650 180 640 196" fill="none" stroke="var(--orange)" stroke-width="3" stroke-dasharray="7 6"/>
      <polygon points="546,110 534,100 532,116" fill="var(--green)"/>
      <polygon points="640,196 632,184 648,186" fill="var(--orange)"/>
    </svg>
    <p class="callout solar">Solar Garden Produces Energy which becomes Utility Credits</p>
    <p class="callout credits">Credits Available for Tenants’ Utility Bills</p>
    <p class="callout signup">Sign Up to Receive Utility Bill Credits. Save 5%</p>
  </section>

  <section class="how-steps">
    <div class="how-step">
      <h3>Join a Solar Farm</h3>
      <p>Join a nearby Community Solar Farm that produces 100% clean solar energy on your behalf</p>
    </div>
    <div class="how-step">
      <h3>Get Utility Bill Credits</h3>
      <p>Every month you will see credits on your utility bill based on the power produced by your share of the solar farm</p>
    </div>
    <div class="how-step">
      <h3>Save Money, Breathe Easier</h3>
      <p>Save on your current utility bill while leading the way to a clean energy Maryland</p>
    </div>
  </section>

  <section class="offer-band">
    <h2>Discount-Price Electricity Offer</h2>
    <p>Save 5% on your Electricity Cost</p>
  </section>

  <section class="signup-steps">
    <div class="step-label step-one">Step 1</div>
    <p class="step-text one">Sign Up for the Solar Subscription Agreement.<br>It runs only for as long as you lease your space</p>
    <span class="guarantee">Your Discount is Guaranteed</span>

    <svg class="hex-center" width="140" height="160" viewBox="0 0 140 160" aria-hidden="true">
      <polygon points="70,4 134,42 134,118 70,156 6,118 6,42" fill="none" stroke="var(--line)" stroke-width="3"/>
      <polygon points="70,28 112,52 112,108 70,132 28,108 28,52" fill="var(--sky)"/>
      <rect x="52" y="56" width="36" height="50" rx="5" fill="none" stroke="var(--band)" stroke-width="3"/>
      <path d="M73 64 L62 84 H72 L66 100 L80 78 H70 Z" fill="var(--orange)"/>
      <line x1="140" y1="80" x2="170" y2="80" stroke="var(--line)" stroke-width="3"/>
    </svg>

    <div class="step-label step-two">Step 2</div>
    <div class="panel-art" role="img" aria-label="Solar panels under a bright sun"></div>
    <p class="step-text two">Securely Provide Sunfield Power with your Utility information through MeterLink.<br>We use the information only to credit your bill, generate your invoice, and provide clean discounted energy.</p>
  </section>

  <section class="benefits">
    <div class="benefit">
      <svg width="34" height="34" viewBox="0 0 34 34" aria-hidden="true"><circle cx="17" cy="17" r="16" fill="var(--orange)"/><path d="M10 17 l5 5 l9 -10" stroke="#fff" stroke-width="3" fill="none"/></svg>
      Save on your Utility bill
    </div>
    <div class="benefit">
      <svg width="34" height="34" viewBox="0 0 34 34" aria-hidden="true"><circle cx="17" cy="17" r="16" fill="var(--orange)"/><path d="M10 17 l5 5 l9 -10" stroke="#fff" stroke-width="3" fill="none"/></svg>
      No upfront costs or payments
    </div>
    <div class="benefit">
      <svg width="34" height="34" viewBox="0 0 34 34" aria-hidden="true"><circle cx="17" cy="17" r="16" fill="var(--orange)"/><path d="M10 17 l5 5 l9 -10" stroke="#fff" stroke-width="3" fill="none"/></svg>
      No changes to your current Utility relationship
    </div>
    <div class="benefit">
      <svg width="34" height="34" viewBox="0 0 34 34" aria-hidden="true"><circle cx="17" cy="17" r="16" fill="var(--orange)"/><path d="M10 17 l5 5 l9 -10" stroke="#fff" stroke-width="3" fill="none"/></svg>
      No equipment, installation or maintenance
    </div>
  </section>

  <nav class="cta">
    <a class="learn" href="#learn">
      <svg width="26" height="26" viewBox="0 0 26 26" aria-hidden="true"><path d="M9 3 v12 l-3 -2 l-2 2 l6 8 h10 l2 -9 l-8 -2 v-9 z" fill="#fff"/></svg>
      Click here<br>to learn
    </a>
    <a class="contact" href="#contact">Contact Us</a>
  </nav>

  <footer class="footer">
    <div class="brand"><span class="brand-dot"></span>Brightleaf Solar</div>
    <div class="copyright">© 2019 All Rights Reserved</div>
  </footer>
</body>
</html>
```